Theme and starter template for small business powerpoint deck

We are starting a technology consulting company and would like to have a powerpoint/google slide theme and initial template. We are more concerned with the theme/colors at this point. Initial template can be pretty simple. We would want a cover slide, agenda slide, some content slides including text content, image content, a combination of both, etc. A closing slide. we have included jpg files of our logo, let us know if you would prefer eps/vector. I assume you may want exact color data as well?

Target Market(s)

Technology and Customer Experience Leadership at companies with 25 or more employees

Industry/Entity Type

Technology Consulting

Font styles to use
Sans Serif

Colors
0054AA
0677BA
7BADD7
CADEEF
E8F1F8

Requirements
Must have
• I have attached JPG and EPS and vector files to project. I would like to stay with those colors but open to slight variation if recommended.

```html
<!DOCTYPE html>
<html lang="en">
<head>
<meta charset="utf-8">
<title>Vantoriq Slide Theme</title>
<link href="https://fonts.googleapis.com/css2?family=Lato:wght@400;700;900&display=swap" rel="stylesheet">
<style>
:root{
  --board:#878787;
  --blue:#0054aa;
  --blue-mid:#0677ba;
  --blue-soft:#7badd7;
  --blue-pale:#cadeef;
  --blue-mist:#e8f1f8;
  --ink:#0d1f33;
  --text:#5e6b78;
  --paper:#ffffff;
}
*{margin:0;padding:0;box-sizing:border-box}
html,body{width:1053px;height:1200px;overflow:hidden;background:var(--board)}
body{position:relative;font-family:'Lato',sans-serif;color:var(--ink)}
.slide{position:absolute;width:445px;height:250px;overflow:hidden;
  background:linear-gradient(135deg,var(--paper) 0%,#f7fafd 45%,var(--blue-mist) 100%)}
.col-l{left:70px}.col-r{left:538px}
.row-1{top:67px}.row-2{top:339px}.row-3{top:610px}.row-4{top:882px}
svg.layer{position:absolute;left:0;top:0;width:445px;height:250px}
.slide-title{position:absolute;left:36px;top:20px;font-weight:900;font-size:20px;letter-spacing:.2px;line-height:1}
.brand-mini{position:absolute;right:8px;top:12px;display:flex;align-items:center;gap:2px;font-weight:900;font-size:4.6px;letter-spacing:.3px}
.brand-mini i{width:4px;height:4px;background:var(--blue);display:block}
.page{position:absolute;left:421px;top:228px;width:12px;height:12px;background:var(--blue-mid);transform:rotate(45deg)}
.page-num{position:absolute;left:419px;top:230px;width:16px;text-align:center;font-size:5px;font-weight:700;color:#fff;line-height:8px}
.page.light{background:#fff}.page-num.light{color:var(--blue)}
.footer{position:absolute;left:0;bottom:0;width:374px;height:16px;background:var(--blue);
  clip-path:polygon(0 0,366px 0,374px 16px,0 16px);color:#fff;font-size:4.8px;display:flex;align-items:center}
.footer span{position:absolute;display:flex;align-items:center;gap:3px}
.footer b{width:6px;height:6px;background:#fff;transform:rotate(45deg);display:block}
.footer .sep{width:.5px;height:8px;background:rgba(255,255,255,.6)}
.para{position:absolute;font-size:6.2px;line-height:10.4px;color:var(--text);text-align:justify}
.list{position:absolute;list-style:none}
.list li{position:relative;padding-left:12px;font-size:6.8px;height:14.2px;line-height:8px}
.list li::before{content:"";position:absolute;left:1px;top:2px;width:4px;height:4px;background:var(--blue-soft);transform:rotate(45deg)}
.bold li{font-weight:700}
.cover-brand{position:absolute;left:276px;top:98px;display:flex;align-items:center;gap:4px;font-weight:900;font-size:13px;letter-spacing:.6px}
.cover-brand i{width:9px;height:9px;background:var(--blue);display:block}
.cover-title{position:absolute;left:276px;top:128px;font-weight:900;font-size:21.5px;line-height:23px}
.date-btn{position:absolute;left:276px;top:190px;width:114px;height:25px;background:var(--blue);color:#fff;
  font-weight:700;font-size:10.5px;letter-spacing:.3px;display:flex;align-items:center;justify-content:center}
.why-title{position:absolute;font-weight:700;font-size:10px;color:var(--blue-mid)}
.why-text{position:absolute;font-size:6.2px;line-height:10.3px;color:var(--text);text-align:right}
.svc-label{position:absolute;font-weight:700;font-size:13px;color:var(--ink);transform:translateX(-50%);white-space:nowrap}
.grad{background:linear-gradient(125deg,var(--blue-soft) 0%,var(--blue-mid) 40%,var(--blue) 100%)}
.grad-thanks{background:linear-gradient(120deg,var(--blue-soft) 0%,var(--blue-mid) 35%,var(--blue) 100%)}
.divider-brand{position:absolute;left:0;width:445px;top:104px;text-align:center;font-weight:900;font-size:11px;color:#fff;letter-spacing:.8px}
.divider-title{position:absolute;left:0;width:445px;top:135px;text-align:center;font-weight:900;font-size:21px;color:#fff}
.divider-sub{position:absolute;left:0;width:445px;top:168px;text-align:center;font-weight:700;font-size:9.5px;color:#fff}
.thanks-title{position:absolute;left:45px;top:56px;font-weight:900;font-size:22px;color:#fff}
.contact{position:absolute;left:45px;display:flex;align-items:center;gap:12px;color:#fff;font-size:8.6px;letter-spacing:.4px;line-height:9.5px}
.contact b{width:11px;height:11px;background:#fff;transform:rotate(45deg);display:block;flex:none;margin-left:3px}
</style>
</head>
<body>

<section class="slide col-l row-1">
  <svg class="layer" viewBox="0 0 445 250">
    <defs>
      <linearGradient id="cvB" x1="0" y1="0" x2="1" y2="1"><stop offset="0" stop-color="#0677ba"/><stop offset="1" stop-color="#003a78"/></linearGradient>
      <linearGradient id="cvG" x1="0" y1="0" x2="1" y2="1"><stop offset="0" stop-color="#cadeef"/><stop offset="1" stop-color="#5d8cb8"/></linearGradient>
      <linearGradient id="cvR" x1="0" y1="0" x2="1" y2="1"><stop offset="0" stop-color="#7badd7"/><stop offset="1" stop-color="#0677ba"/></linearGradient>
    </defs>
    <polygon points="144,0 217,126 70,126" fill="url(#cvB)" role="img" aria-label="Photo of two colleagues reviewing work, blue tint"/>
    <polygon points="70,126 144,250 -4,250" fill="url(#cvG)" role="img" aria-label="Photo of a person at a desk, pale blue tint"/>
    <polygon points="217,126 287,250 144,250" fill="url(#cvR)" role="img" aria-label="Photo of an office workspace, blue tint"/>
  </svg>
  <div class="cover-brand"><i></i>VANTORIQ</div>
  <h1 class="cover-title">PRESENTATION<br>TITLE HERE</h1>
  <div class="date-btn">AUGUST 09,2024</div>
  <div class="page"></div><div class="page-num">01</div>
</section>

<section class="slide col-r row-1">
  <h2 class="slide-title">WHY CHOOSE US</h2>
  <div class="brand-mini"><i></i>VANTORIQ</div>
  <svg class="layer" viewBox="0 0 445 250">
    <polygon points="238,26 311,128 166,128" fill="var(--blue)"/>
    <polygon points="166,128 237,229 92,229" fill="var(--blue-soft)"/>
    <polygon points="311,128 384,229 237,229" fill="var(--blue-mid)"/>
    <line x1="160" y1="63" x2="211" y2="63" stroke="var(--blue)" stroke-width=".8"/><circle cx="160" cy="63" r="1.6" fill="var(--blue)"/>
    <line x1="114" y1="162" x2="137" y2="162" stroke="var(--blue-soft)" stroke-width=".8"/><circle cx="114" cy="162" r="1.6" fill="var(--blue-soft)"/>
    <polyline points="392,154 392,172 343,172" fill="none" stroke="var(--blue-mid)" stroke-width=".8"/><circle cx="392" cy="154" r="1.6" fill="var(--blue-mid)"/>
    <g fill="none" stroke="#fff" stroke-width="1.3" stroke-linecap="round" stroke-linejoin="round">
      <circle cx="238" cy="80" r="7"/><path d="M235 87v4h6v-4M238 73v-3M231 80h-3M248 80h-3"/>
      <circle cx="226" cy="92" r="3"/><path d="M220 104v-4a6 6 0 0 1 12 0v4z"/>
      <circle cx="250" cy="92" r="3"/><path d="M244 104v-4a6 6 0 0 1 12 0v4z"/>
      <rect x="157" y="168" width="14" height="9" rx="2"/><rect x="165" y="163" width="14" height="9" rx="2"/>
      <path d="M152 190h30M158 190v12M176 190v12"/><circle cx="156" cy="183" r="3"/><circle cx="178" cy="183" r="3"/>
      <rect x="300" y="175" width="24" height="16" rx="1.5"/><path d="M296 196h32l-2 3h-28z"/>
      <circle cx="312" cy="183" r="3.5"/><path d="M312 170v5M304 171v4M320 171v4"/>
    </g>
    <rect x="226" y="171" width="4" height="4" fill="var(--blue)"/>
    <text x="232" y="175" font-family="Lato,sans-serif" font-weight="900" font-size="6.5" fill="#0d1f33" letter-spacing=".4">VANTORIQ</text>
  </svg>
  <div class="why-title" style="right:299px;top:56px">TITLE HERE</div>
  <div class="why-text" style="right:299px;top:74px;width:120px">At vero eos et accusamus et iusto ssimos ducimus qui blanditiis praesentium atum deleniti atque corrupti quos dolores et quas molestias excepturisi</div>
  <div class="why-title" style="right:32px;top:78px">TITLE HERE</div>
  <div class="why-text" style="right:32px;top:96px;width:84px">At vero eos et accusamus et iusto ssimos ducimus qui blanditiis praesentium atum deleniti atque corrupti quos</div>
  <div class="why-title" style="right:343px;top:155px">TITLE HERE</div>
  <div class="why-text" style="right:343px;top:172px;width:84px">At vero eos et accusamus et iusto ssimos ducimus qui blanditiis praesentium atum deleniti atque corrupti quos</div>
  <div class="footer">
    <span style="left:37px"><b></b>+1 888 888 8888</span><span class="sep" style="left:103px"></span>
    <span style="left:109px"><b></b>info@companyname.com</span><span class="sep" style="left:194px"></span>
    <span style="left:203px">© 2024 Vantoriq. All rights reserved.Privacy Terms of Use</span>
  </div>
  <div class="page"></div><div class="page-num">05</div>
</section>

<section class="slide col-l row-2">
  <h2 class="slide-title">AGENDA</h2>
  <div class="brand-mini"><i></i>VANTORIQ</div>
  <ul class="list" style="left:36px;top:60px">
    <li>Sed ut perspiciatis unde omnis</li><li>liste natus error sit voluptatem</li><li>Accusantium doloremque</li>
    <li>Llaudantiumtotam rem</li><li>Aperiam eaque ipsa</li><li>Qquae ab illo inventore</li>
  </ul>
  <svg class="layer" viewBox="0 0 445 250">
    <defs>
      <linearGradient id="agB" x1="0" y1="0" x2="1" y2="1"><stop offset="0" stop-color="#0677ba"/><stop offset="1" stop-color="#00336a"/></linearGradient>
      <linearGradient id="agG" x1="0" y1="0" x2="1" y2="1"><stop offset="0" stop-color="#e8f1f8"/><stop offset="1" stop-color="#7badd7"/></linearGradient>
      <linearGradient id="agR" x1="0" y1="0" x2="1" y2="1"><stop offset="0" stop-color="#0054aa"/><stop offset="1" stop-color="#021d3d"/></linearGradient>
    </defs>
    <polygon points="291,8 363,109 217,109" fill="url(#agB)" role="img" aria-label="Illustration of a glowing laptop with data screens"/>
    <polygon points="217,109 290,210 145,210" fill="url(#agG)" role="img" aria-label="Photo of hands typing on a keyboard with network icons"/>
    <polygon points="363,109 437,210 290,210" fill="url(#agR)" role="img" aria-label="Photo of a glowing light bulb on dark background"/>
  </svg>
  <div class="footer">
    <span style="left:37px"><b></b>+1 888 888 8888</span><span class="sep" style="left:103px"></span>
    <span style="left:109px"><b></b>info@companyname.com</span><span class="sep" style="left:194px"></span>
    <span style="left:203px">© 2024 Vantoriq. All rights reserved.Privacy Terms of Use</span>
  </div>
  <div class="page"></div><div class="page-num">02</div>
</section>

<section class="slide col-r row-2">
  <h2 class="slide-title">OUR GRAPH</h2>
  <div class="brand-mini"><i></i>VANTORIQ</div>
  <p class="para" style="left:36px;top:57px;width:159px">At vero eos et accusamus et iusto odio dignissimos ducimus qui blanditiis praesentium voluptatum deleniti atque corrupti quos dolores et quas molestias excepturi sint occaecati cupiditate non provident, similique sunt in culpa qui officia deserunt mollitia animi, id est laborum et dolorum fuga. Et harum quidem rerum facilis est et expedita distinctio. Nam libero tempore, cum soluta nobis est eligendi optio cumque nihil impedit</p>
  <p class="para" style="left:36px;top:151px;width:159px">Qo minus id quod maxime placeat facere possimus, omnis voluptas assumenda est, omnis dolor repellendus. Temporibus autem quibusdam et aut officiis vero eos et accusamus et iusto odio dignissimos ducimus qui blanditiis praesentium voluptatum deleniti atque corrupti quos dolores et quas molestias</p>
  <svg class="layer" viewBox="0 0 445 250" font-family="Lato,sans-serif">
    <g stroke="#d6e3ef" stroke-width=".4">
      <line x1="228" y1="69" x2="427" y2="69"/><line x1="228" y1="89" x2="427" y2="89"/><line x1="228" y1="110" x2="427" y2="110"/>
      <line x1="228" y1="130" x2="427" y2="130"/><line x1="228" y1="150" x2="427" y2="150"/><line x1="228" y1="170" x2="427" y2="170"/>
      <line x1="228" y1="191" x2="427" y2="191"/><line x1="228" y1="69" x2="228" y2="191"/><line x1="427" y1="69" x2="427" y2="191"/>
    </g>
    <g font-size="4" fill="#333" text-anchor="end">
      <text x="224" y="71">120</text><text x="224" y="91">100</text><text x="224" y="112">80</text><text x="224" y="132">60</text>
      <text x="224" y="152">40</text><text x="224" y="172">20</text><text x="224" y="193">0</text>
    </g>
    <g font-size="4" fill="#333" text-anchor="middle">
      <text x="245" y="198">Sun</text><text x="273" y="198">Mon</text><text x="300" y="198">Tue</text><text x="328" y="198">Wed</text>
      <text x="356" y="198">Thu</text><text x="383" y="198">Fri</text><text x="409" y="198">Sat</text>
    </g>
    <g font-size="3.8" fill="#333" text-anchor="middle">
      <rect x="240" y="89" width="5" height="102" fill="var(--blue)"/><text x="242.5" y="87">100</text>
      <rect x="246.5" y="99" width="5" height="92" fill="var(--blue-soft)"/><text x="249" y="97">90</text>
      <rect x="268" y="99" width="5" height="92" fill="var(--blue)"/><text x="270.5" y="97">90</text>
      <rect x="274.5" y="110" width="5" height="81" fill="var(--blue-soft)"/><text x="277" y="108">80</text>
      <rect x="294" y="140" width="5" height="51" fill="var(--blue-soft)"/><text x="296.5" y="138">50</text>
      <rect x="303" y="89" width="5" height="102" fill="var(--blue)"/><text x="305.5" y="87">100</text>
      <rect x="322" y="89" width="5" height="102" fill="var(--blue-soft)"/><text x="324.5" y="87">100</text>
      <rect x="330" y="130" width="5" height="61" fill="var(--blue)"/><text x="332.5" y="128">60</text>
      <rect x="350" y="89" width="5" height="102" fill="var(--blue-soft)"/><text x="352.5" y="87">100</text>
      <rect x="357" y="99" width="5" height="92" fill="var(--blue)"/><text x="359.5" y="97">90</text>
      <rect x="378" y="130" width="5" height="61" fill="var(--blue)"/><text x="380.5" y="128">60</text>
      <rect x="386" y="115" width="5" height="76" fill="var(--blue-soft)"/><text x="388.5" y="113">75</text>
      <rect x="404" y="140" width="5" height="51" fill="var(--blue)"/><text x="406.5" y="138">50</text>
      <rect x="412" y="89" width="5" height="102" fill="var(--blue-soft)"/><text x="414.5" y="87">100</text>
    </g>
  </svg>
  <div class="footer">
    <span style="left:37px"><b></b>+1 888 888 8888</span><span class="sep" style="left:103px"></span>
    <span style="left:109px"><b></b>info@companyname.com</span><span class="sep" style="left:194px"></span>
    <span style="left:203px">© 2024 Vantoriq. All rights reserved.Privacy Terms of Use</span>
  </div>
  <div class="page"></div><div class="page-num">06</div>
</section>

<section class="slide col-l row-3">
  <h2 class="slide-title">ABOUT US</h2>
  <div class="brand-mini"><i></i>VANTORIQ</div>
  <p class="para" style="left:36px;top:56px;width:218px">At vero eos et accusamus et iusto odio dignissimos ducimus qui blanditiis praesentium voluptatum deleniti atque corrupti quos dolores et quas molestias excepturi sint occaecati cupiditate non provident, similique sunt in culpa qui officia deserunt mollitia animi, id est laborum et dolorum fuga. Et harum quidem rerum facilis est et expedita distinctio. Nam libero tempore, cum soluta nobis est eligendi optio cumque nihil impedit quo minus id quod maxime placeat facere possimus, omnis voluptas assumenda est, omnis dolor repellendus. Temporibus autem quibusdam et aut officiis</p>
  <p class="para" style="left:36px;top:160px;width:218px">At vero eos et accusamus et iusto odio dignissimos ducimus qui blanditiis praesentium voluptatum deleniti atque corrupti quos dolores et quas molestias excepturi sint occaecati cupiditate non provident, similique sunt in culpa qui officia deserunt mollitia animi, id est laborum</p>
  <ul class="list bold" style="left:296px;top:57px">
    <li>Sed ut perspiciatis unde omnis</li><li>liste natus error sit voluptatem</li><li>Accusantium doloremque</li>
    <li>Llaudantiumtotam rem</li><li>Aperiam eaque ipsa</li><li>Qquae ab illo inventore</li>
    <li>Sed ut perspiciatis unde omnis</li><li>liste natus error sit voluptatem</li><li>Accusantium doloremque</li>
    <li>Llaudantiumtotam rem</li>
  </ul>
  <div class="footer">
    <span style="left:37px"><b></b>+1 888 888 8888</span><span class="sep" style="left:103px"></span>
    <span style="left:109px"><b></b>info@companyname.com</span><span class="sep" style="left:194px"></span>
    <span style="left:203px">© 2024 Vantoriq. All rights reserved.Privacy Terms of Use</span>
  </div>
  <div class="page"></div><div class="page-num">03</div>
</section>

<section class="slide col-r row-3">
  <h2 class="slide-title">OUR SERVICES</h2>
  <div class="brand-mini"><i></i>VANTORIQ</div>
  <svg class="layer" viewBox="0 0 445 250">
    <defs>
      <linearGradient id="svA" x1="0" y1="0" x2="1" y2="1"><stop offset="0" stop-color="#2f5f8f"/><stop offset="1" stop-color="#0b2240"/></linearGradient>
      <linearGradient id="svB" x1="0" y1="0" x2="1" y2="1"><stop offset="0" stop-color="#cadeef"/><stop offset="1" stop-color="#1f4f80"/></linearGradient>
      <linearGradient id="svC" x1="0" y1="0" x2="1" y2="1"><stop offset="0" stop-color="#0677ba"/><stop offset="1" stop-color="#06294a"/></linearGradient>
    </defs>
    <polygon points="196,0 250,0 224,46" fill="var(--blue)"/>
    <polygon points="0,82 52,110 0,143" fill="var(--blue-soft)"/>
    <polygon points="445,84 397,113 445,142" fill="var(--blue-mid)"/>
    <polygon points="93,62 170,191 14,191" fill="url(#svA)" role="img" aria-label="Photo of two colleagues in a data center"/>
    <polygon points="144,84 300,84 222,214" fill="url(#svB)" role="img" aria-label="Photo of hands analysing charts on a screen"/>
    <polygon points="353,62 431,191 275,191" fill="url(#svC)" role="img" aria-label="Photo of a phone showing security icons"/>
  </svg>
  <div class="svc-label" style="left:222px;top:59px">Lliberempore</div>
  <div class="svc-label" style="left:92px;top:203px">Nerempore</div>
  <div class="svc-label" style="left:352px;top:203px">Soluta nobis</div>
  <div class="footer">
    <span style="left:37px"><b></b>+1 888 888 8888</span><span class="sep" style="left:103px"></span>
    <span style="left:109px"><b></b>info@companyname.com</span><span class="sep" style="left:194px"></span>
    <span style="left:203px">© 2024 Vantoriq. All rights reserved.Privacy Terms of Use</span>
  </div>
  <div class="page"></div><div class="page-num">07</div>
</section>

<section class="slide col-l row-4 grad">
  <div class="divider-brand">VANTORIQ</div>
  <h2 class="divider-title">SECTION DIVIDER TITLE</h2>
  <p class="divider-sub">Nam libero tempoum soluta nobis est</p>
  <div class="page light"></div><div class="page-num light">04</div>
</section>

<section class="slide col-r row-4 grad-thanks">
  <h2 class="thanks-title">THANK YOU</h2>
  <div class="contact" style="top:99px"><b></b><span>234,Nam libero tempoum<br>soluta nobis est</span></div>
  <div class="contact" style="top:131px"><b></b><span>+1 888 888 8888</span></div>
  <div class="contact" style="top:162px"><b></b><span>info@companyname.com</span></div>
  <svg class="layer" viewBox="0 0 445 250">
    <defs>
      <linearGradient id="tyA" x1="0" y1="0" x2="1" y2="1"><stop offset="0" stop-color="#cadeef"/><stop offset="1" stop-color="#2a4e75"/></linearGradient>
      <linearGradient id="tyB" x1="0" y1="0" x2="1" y2="1"><stop offset="0" stop-color="#e8f1f8"/><stop offset="1" stop-color="#0677ba"/></linearGradient>
      <linearGradient id="tyC" x1="0" y1="0" x2="1" y2="1"><stop offset="0" stop-color="#7badd7"/><stop offset="1" stop-color="#003f80"/></linearGradient>
    </defs>
    <polygon points="311,10 364,111 258,111" fill="url(#tyA)" role="img" aria-label="Photo of a person working at a laptop"/>
    <polygon points="258,111 311,211 194,211" fill="url(#tyB)" role="img" aria-label="Illustration of a glowing digital city grid"/>
    <polygon points="364,111 426,211 311,211" fill="url(#tyC)" role="img" aria-label="Illustration of a glowing digital city grid"/>
  </svg>
  <div class="page light"></div><div class="page-num light">08</div>
</section>

</body>
</html>
```